Frostvale Harborline LLC

we need a business card design

Industry/Entity Type

hvac

Contact Information for Business Card

my logo

Requirements
Must have
• my logo and same colors

```html
<!DOCTYPE html>
<html lang="en">
<head>
<meta charset="UTF-8">
<title>Frostvale Harborline LLC – Business Card</title>
<link href="https://fonts.googleapis.com/css2?family=Montserrat:wght@400;500;700;800&display=swap" rel="stylesheet">
<style>
  :root {
    --stage: #3a3a3c;
    --card-blue: #0f5fa9;
    --sky: #14b0e3;
    --amber: #f7b548;
    --white: #ffffff;
  }
  * { margin: 0; padding: 0; box-sizing: border-box; }
  html, body { width: 1200px; height: 875px; overflow: hidden; }
  body {
    background: var(--stage);
    font-family: "Montserrat", sans-serif;
    display: flex;
    align-items: center;
    justify-content: center;
    gap: 40px;
  }
  .card {
    position: relative;
    width: 540px;
    height: 308px;
    border-radius: 18px;
    background: var(--card-blue);
    overflow: hidden;
    color: var(--white);
  }
  .brand-lockup {
    position: absolute;
    display: flex;
    align-items: center;
    gap: 12px;
  }
  .brand-mark {
    flex: none;
    border-radius: 50%;
    background: var(--amber);
  }
  .brand-name {
    font-weight: 800;
    color: var(--white);
    text-transform: uppercase;
    line-height: 1.1;
  }
  .card-front .brand-lockup {
    left: 50%; top: 50%;
    transform: translate(-50%, -50%);
  }
  .card-front .brand-mark { width: 40px; height: 40px; }
  .card-front .brand-name { font-size: 28px; white-space: nowrap; }

  .back-wave { position: absolute; inset: 0; width: 100%; height: 100%; }
  .card-back .brand-lockup { right: 26px; top: 48px; }
  .card-back .brand-mark { width: 26px; height: 26px; }
  .card-back .brand-name { font-size: 19px; }

  .identity {
    position: absolute;
    left: 0; top: 84px;
    padding-left: 40px;
  }
  .identity::before {
    content: "";
    position: absolute;
    left: 14px; top: 4px;
    width: 12px; height: 34px;
    background: var(--sky);
  }
  .person-name { font-size: 22px; font-weight: 800; letter-spacing: 0.3px; }
  .person-name .first { color: var(--sky); }
  .person-name .last { color: var(--amber); }
  .person-role { font-size: 13px; font-weight: 400; margin-top: 2px; }

  .address {
    position: absolute;
    left: 58px; top: 140px;
    font-size: 12.5px; line-height: 1.45;
  }
  .contact-list {
    position: absolute;
    left: 58px; top: 186px;
    list-style: none;
    font-size: 12.5px;
  }
  .contact-list li { display: flex; align-items: center; gap: 8px; line-height: 1.6; }
  .contact-list svg { width: 11px; height: 11px; flex: none; }
</style>
</head>
<body>

  <section class="card card-front" aria-label="Card front">
    <div class="brand-lockup">
      <span class="brand-mark"></span>
      <span class="brand-name">Frostvale<br>Harborline LLC</span>
    </div>
  </section>

  <section class="card card-back" aria-label="Card back">
    <svg class="back-wave" viewBox="0 0 540 308" preserveAspectRatio="none" aria-hidden="true">
      <path d="M0 308 L0 296 C200 304 320 278 395 198 C440 150 490 126 540 120 L540 308 Z" fill="var(--sky)"/>
      <path d="M0 289 C200 297 320 271 395 191 C440 143 490 119 540 113" fill="none" stroke="var(--amber)" stroke-width="7"/>
    </svg>

    <div class="brand-lockup">
      <span class="brand-mark"></span>
      <span class="brand-name">Frostvale<br>Harborline LLC</span>
    </div>

    <div class="identity">
      <p class="person-name"><span class="first">DALEN</span> <span class="last">MARSH</span></p>
      <p class="person-role">Founder</p>
    </div>

    <p class="address">24 Quarry Ridge Ln<br>Eastmere XYZ 4012</p>

    <ul class="contact-list">
      <li>
        <svg viewBox="0 0 12 12"><path d="M2.5 1 L4.5 1 L5.3 3.6 L4 4.6 C4.7 6 6 7.3 7.4 8 L8.4 6.7 L11 7.5 L11 9.5 C11 10.4 10.3 11 9.5 11 C5 11 1 7 1 2.5 C1 1.7 1.6 1 2.5 1 Z" fill="var(--amber)"/></svg>
        303.555.0147
      </li>
      <li>
        <svg viewBox="0 0 12 12"><rect x="0.5" y="2" width="11" height="8" fill="var(--amber)"/><path d="M0.5 2 L6 6.5 L11.5 2" fill="none" stroke="var(--card-blue)" stroke-width="1"/></svg>
        info@frostvaleharborline.com
      </li>
      <li>
        <svg viewBox="0 0 12 12"><circle cx="6" cy="6" r="5" fill="none" stroke="var(--amber)" stroke-width="1.2"/><path d="M1 6 H11 M6 1 C3.5 3.5 3.5 8.5 6 11 M6 1 C8.5 3.5 8.5 8.5 6 11" fill="none" stroke="var(--amber)" stroke-width="1"/></svg>
        www.frostvaleharborline.com
      </li>
    </ul>
  </section>

</body>
</html>
```